Covid 19 Exit Strategy one page brochure

I would like to design, and will need URGENT help, a brochure detailing a Covid 19 Exit Strategy plan. This brochure will need to be understood easily and the graphics inside should make it easy for people to understand without reading the entire text. This project is quite urgent and needs to be completed THIS WEEK - by Saturday may 16th at the latest. I am attaching two examples. I will provide the text.

```html
<!DOCTYPE html>
<html lang="en">
<head>
<meta charset="utf-8">
<title>Phased Lockdown Exit Strategy Plan</title>
<link href="https://fonts.googleapis.com/css2?family=Montserrat:wght@300;400;500;600;700;800;900&display=swap" rel="stylesheet">
<style>
  :root {
    --page-bg: #b9b9b9;
    --panel-bg: #ffffff;
    --cell-grey: #ececec;
    --navy: #1f2366;
    --navy-deep: #141742;
    --red: #d2232a;
    --red-bright: #e3242b;
    --charcoal: #262626;
    --ink: #231f20;
    --ring: #a3a3a3;
    --red-tint: #f4d6d7;
    --navy-tint: #d9daea;
  }
  * { margin: 0; padding: 0; box-sizing: border-box; }
  html, body { width: 1200px; height: 3347px; overflow: hidden; }
  body { background: var(--page-bg); font-family: "Montserrat", Arial, sans-serif; color: var(--ink); position: relative; }

  .sheet { position: absolute; left: 100px; top: 108px; width: 1000px; height: 3130px; background: var(--panel-bg); overflow: hidden; }

  .hero { position: absolute; left: 0; top: 0; width: 1000px; height: 302px;
    background: radial-gradient(ellipse at 50% 40%, #2b3183 0%, #1c2063 55%, var(--navy-deep) 100%); }
  .hero-title { position: absolute; top: 36px; width: 100%; text-align: center; color: var(--red-bright);
    font-weight: 800; font-size: 57px; letter-spacing: 0.5px; line-height: 60px; }
  .hero-intro { position: absolute; left: 57px; top: 116px; width: 886px; color: #fff; font-size: 16.6px;
    line-height: 22.2px; text-align: justify; text-align-last: center; font-weight: 400; }

  .plan-band { position: absolute; left: 0; top: 302px; width: 1000px; height: 232px;
    background: linear-gradient(100deg, #b71c22 0%, var(--red) 45%, #c11e25 100%); }
  .plan-sub { position: absolute; top: 330px; width: 100%; text-align: center; color: #fff; font-weight: 400; font-size: 43px; line-height: 50px; }
  .plan-title { position: absolute; top: 380px; width: 100%; text-align: center; color: #fff; font-weight: 800; font-size: 47px; line-height: 54px; }

  .stage-pill { position: absolute; left: 212px; top: 461px; width: 737px; height: 140px; background: var(--charcoal);
    border-radius: 26px; color: #fff; font-size: 20.5px; line-height: 28px; font-weight: 500; padding: 28px 30px 0 78px; }
  .stage-badge { position: absolute; left: 52px; top: 431px; width: 202px; height: 202px; }

  .sequence-heading { position: absolute; top: 678px; width: 100%; text-align: center; font-weight: 600; font-size: 26.5px; line-height: 34px; color: var(--ink); }
  .sequence-rule { position: absolute; left: 0; top: 680px; width: 1000px; height: 80px; }

  .cell { position: absolute; }
  .cell.grey { background: var(--cell-grey); }
  .cell.dark { background: var(--charcoal); color: #fff; }
  .icon { position: absolute; width: 120px; height: 120px; }
  .cell-text { position: absolute; font-size: 19.6px; line-height: 26.2px; font-weight: 400; }
  .col-left .icon { left: 46px; }
  .col-left .cell-text { left: 200px; width: 300px; }
  .col-right .icon { left: 30px; }
  .col-right .cell-text { left: 183px; width: 295px; }
  .wide .icon { left: 46px; }
  .wide .cell-text { width: 726px; text-align: justify; }
  .transport-art { position: absolute; left: 49px; top: 49px; width: 120px; height: 174px; border-radius: 10px;
    background: linear-gradient(160deg, #e0343a, #b81c22); }
</style>
</head>
<body>
<div class="sheet">

  <header class="hero">
    <h1 class="hero-title">CORONAVIRUS COVID-19</h1>
    <p class="hero-intro">Pandemics have, historically, seen their end both medically - via herd immunity or immunizations. And while there are several clinical trials underway for potential Covid-19 vaccines, we are still a long way from deploying an effective vaccine and one that will stand the test of time as the virus changes. Covid-19 pandemic will be considered ‘ended’ when there are only occasional traces of localized cases that are quickly contained in specific locations., Today and in the absence of an effective vaccine(s) and for the re-opening of the economies and social activities to be successful, it is critical that the following basic conditions be in place before any lockdowns are lifted and before social activities resume:</p>
  </header>

  <section class="plan-band" role="img" aria-label="Red banner backdrop with virus particle imagery"></section>
  <h2 class="plan-sub">PHASED LOCKDOWN</h2>
  <h2 class="plan-title">EXIT STRATEGY PLAN</h2>

  <div class="stage-pill">To enter this stage, additional to the general requirements, the Effective Reproduction Number (Rt) must be less than 1 and the death rate at less than 3%.</div>
  <svg class="stage-badge" viewBox="0 0 202 202" aria-label="Stage 1">
    <defs><clipPath id="stage-disc"><circle cx="101" cy="101" r="88"/></clipPath></defs>
    <circle cx="101" cy="101" r="101" fill="#fff"/>
    <circle cx="101" cy="101" r="88" fill="var(--charcoal)"/>
    <rect x="0" y="136" width="202" height="38" fill="var(--red)" clip-path="url(#stage-disc)"/>
    <text x="101" y="128" text-anchor="middle" font-family="Montserrat, sans-serif" font-weight="900" font-size="140" fill="var(--red)">1</text>
    <text x="101" y="165" text-anchor="middle" font-family="Montserrat, sans-serif" font-weight="800" font-size="26" fill="#fff">STAGE</text>
  </svg>

  <svg class="sequence-rule" viewBox="0 0 1000 80">
    <polyline points="0,115 169,115 210,177" transform="translate(0,-115)" fill="none" stroke="var(--navy)" stroke-width="2"/>
    <polyline points="790,115 831,177 1000,177" transform="translate(0,-115)" fill="none" stroke="var(--navy)" stroke-width="2"/>
  </svg>
  <h3 class="sequence-heading">THE ECONOMY AND SOCIAL ACTIVITIES<br>CAN RESUME IN THIS SEQUENCE:</h3>

  <!-- Row 1 -->
  <div class="cell col-left grey" style="left:0;top:810px;width:500px;height:183px;">
    <div class="icon" style="top:26px;"><svg viewBox="0 0 120 120" role="img" aria-label="Icon of an elderly person resting on a bench"><circle cx="60" cy="60" r="57" fill="#fff" stroke="var(--ring)" stroke-width="3"/><circle cx="60" cy="60" r="38" fill="var(--red-tint)"/></svg></div>
    <p class="cell-text" style="top:34px;">Elderly (60+ years old)&nbsp; and vulnerable individuals should continue to self-isolate.</p>
  </div>
  <div class="cell col-right" style="left:500px;top:810px;width:500px;height:183px;">
    <div class="icon" style="top:26px;"><svg viewBox="0 0 120 120" role="img" aria-label="Icon of people spread apart with arrows"><circle cx="60" cy="60" r="57" fill="#fff" stroke="var(--ring)" stroke-width="3"/><circle cx="60" cy="60" r="38" fill="var(--navy-tint)"/></svg></div>
    <p class="cell-text" style="top:34px;">No more than 5 people maximum gathering at a time in public areas and at work.</p>
  </div>

  <!-- Row 2 -->
  <div class="cell col-left" style="left:0;top:993px;width:500px;height:185px;">
    <div class="icon" style="top:23px;"><svg viewBox="0 0 120 120" role="img" aria-label="Icon of a person working at a desk"><circle cx="60" cy="60" r="57" fill="#fff" stroke="var(--ring)" stroke-width="3"/><circle cx="60" cy="60" r="38" fill="var(--red-tint)"/></svg></div>
    <p class="cell-text" style="top:44px;">Work from home should continue whenever and as much as possible.</p>
  </div>
  <div class="cell col-right grey" style="left:500px;top:993px;width:500px;height:185px;">
    <div class="icon" style="top:23px;"><svg viewBox="0 0 120 120" role="img" aria-label="Icon of three people standing apart"><circle cx="60" cy="60" r="57" fill="#fff" stroke="var(--ring)" stroke-width="3"/><circle cx="60" cy="60" r="38" fill="var(--navy-tint)"/></svg></div>
    <p class="cell-text" style="top:29px;">Social distancing should continue to be re-enforced in public areas, at work &amp; in all areas reopened.</p>
  </div>

  <!-- Row 3 -->
  <div class="cell col-left grey" style="left:0;top:1178px;width:500px;height:262px;">
    <div class="icon" style="top:23px;"><svg viewBox="0 0 120 120" role="img" aria-label="Icon of a car and a traveller with luggage"><circle cx="60" cy="60" r="57" fill="#fff" stroke="var(--ring)" stroke-width="3"/><circle cx="60" cy="60" r="38" fill="var(--red-tint)"/></svg></div>
    <p class="cell-text" style="top:30px;">Non-essential travel should be minimized between cities and regions (and within cities and regions where covid-19 infections are still a risk)</p>
  </div>
  <div class="cell col-right" style="left:500px;top:1178px;width:500px;height:262px;">
    <div class="icon" style="top:23px;"><svg viewBox="0 0 120 120" role="img" aria-label="Icon of a cafeteria table with umbrella and chairs"><circle cx="60" cy="60" r="57" fill="#fff" stroke="var(--ring)" stroke-width="3"/><circle cx="60" cy="60" r="38" fill="var(--navy-tint)"/></svg></div>
    <p class="cell-text" style="top:27px;">Large businesses (300 people &amp; more, manufacturing, services, etc.) can reopen progressively. Common areas should remain closed (cafeteria, restaurant, gym, meeting rooms of no more than 5 people).</p>
  </div>

  <!-- Row 4 -->
  <div class="cell col-left" style="left:0;top:1440px;width:500px;height:273px;">
    <div class="icon" style="top:26px;"><svg viewBox="0 0 120 120" role="img" aria-label="Icon of a small shop front"><circle cx="60" cy="60" r="57" fill="#fff" stroke="var(--ring)" stroke-width="3"/><circle cx="60" cy="60" r="38" fill="var(--red-tint)"/></svg></div>
    <p class="cell-text" style="top:32px;">Small businesses (300 people and less) can reopen as well with the same conditions as large businesses.</p>
  </div>
  <div class="cell col-right grey" style="left:500px;top:1440px;width:500px;height:273px;">
    <div class="icon" style="top:26px;"><svg viewBox="0 0 120 120" role="img" aria-label="Icon of a shopping cart"><circle cx="60" cy="60" r="57" fill="#fff" stroke="var(--ring)" stroke-width="3"/><circle cx="60" cy="60" r="38" fill="var(--navy-tint)"/></svg></div>
    <p class="cell-text" style="top:30px;">Commercial shops can reopen. Shops should control the flow of people in their facilities not to exceed 30% at a time of standard capacity. Shops should provide disinfectant and temperature control at entry.</p>
  </div>

  <!-- Pharmacies -->
  <div class="cell wide" style="left:0;top:1713px;width:1000px;height:192px;">
    <div class="icon" style="top:39px;"><svg viewBox="0 0 120 120" role="img" aria-label="Icon of a pharmacist and client at a counter"><circle cx="60" cy="60" r="57" fill="#fff" stroke="var(--ring)" stroke-width="3"/><circle cx="60" cy="60" r="38" fill="var(--navy-tint)"/></svg></div>
    <p class="cell-text" style="left:217px;top:48px;">Pharmacies will continue to be open. However, they must make available disinfectant for use by clients and will continue to comply with social distancing. Pharmacies should limit the number of client/patient in their stores not to exceed 30% of the standard capacity.</p>
  </div>

  <!-- Transportation -->
  <div class="cell wide dark" style="left:0;top:1905px;width:1000px;height:273px;">
    <div class="transport-art" role="img" aria-label="Illustration of a train, plane, taxi and bus"></div>
    <p class="cell-text" style="left:226px;top:31px;">Transportation (buses, taxis, airlines) will resume progressively. No air travels permitted in and out of Covid-19 known hotspots, locally or internationally. Entry to country should be limited and strictly controlled. All landing passengers and visitors regardless of the country of origin should be tested for Covid-19 at arrival. All passengers and visitors will undergo a temperature check at arrival. No more than 3 people at a time in a taxi/rydo including the driver. All passengers wearing masks. Buses should operate with no more than 30% customer’s capacity per bus.</p>
  </div>

  <!-- Religious sites -->
  <div class="cell wide" style="left:0;top:2178px;width:1000px;height:202px;">
    <div class="icon" style="top:35px;"><svg viewBox="0 0 120 120" role="img" aria-label="Icon of a person wearing a mask"><circle cx="60" cy="60" r="57" fill="#fff" stroke="var(--ring)" stroke-width="3"/><circle cx="60" cy="60" r="38" fill="var(--navy-tint)"/></svg></div>
    <p class="cell-text" style="left:226px;top:35px;">Religious sites can reopen with a maximum capacity of 30% or less. Social distancing and wearing masks is mandatory. Religious sites should organize (volunteers can help) to check body temperature of everyone accessing the site and provide disinfectant at entry.</p>
  </div>

  <!-- Hotels / Coffee -->
  <div class="cell col-left grey" style="left:0;top:2380px;width:500px;height:338px;">
    <div class="icon" style="top:34px;"><svg viewBox="0 0 120 120" role="img" aria-label="Icon of a hotel guest with luggage at a reception desk"><circle cx="60" cy="60" r="57" fill="#fff" stroke="var(--ring)" stroke-width="3"/><circle cx="60" cy="60" r="38" fill="var(--red-tint)"/></svg></div>
    <p class="cell-text" style="top:42px;">Hotels &amp; tourism (museums, etc.) can reopen but must operate at 30% or less capacity. All common areas (restaurants, gyms, swimming pools, conference rooms, etc.) should remain closed.</p>
  </div>
  <div class="cell col-right" style="left:500px;top:2380px;width:500px;height:338px;">
    <div class="icon" style="top:34px;"><svg viewBox="0 0 120 120" role="img" aria-label="Icon of two people seated at a cafe table"><circle cx="60" cy="60" r="57" fill="#fff" stroke="var(--ring)" stroke-width="3"/><circle cx="60" cy="60" r="38" fill="var(--navy-tint)"/></svg></div>
    <p class="cell-text" style="top:44px;">Coffee &amp; restaurants can reopen but must operate at 30% capacity as well and comply with social distanc-ing. Clients must wear as much as possible their masks if they are not con-suming food/coffee. Clients should avoid to talking to each other with masks off.</p>
  </div>

  <!-- Schools / Events -->
  <div class="cell col-left" style="left:0;top:2718px;width:500px;height:364px;">
    <div class="icon" style="top:43px;"><svg viewBox="0 0 120 120" role="img" aria-label="Icon of a laptop showing a graduation cap"><circle cx="60" cy="60" r="57" fill="#fff" stroke="var(--ring)" stroke-width="3"/><circle cx="60" cy="60" r="38" fill="var(--red-tint)"/></svg></div>
    <p class="cell-text" style="top:51px;">All schools should remain closed. On-line courses should continue be the preferred method for education.</p>
  </div>
  <div class="cell col-right grey" style="left:500px;top:2718px;width:500px;height:364px;">
    <div class="icon" style="top:43px;"><svg viewBox="0 0 120 120" role="img" aria-label="Icon of an audience facing a screen"><circle cx="60" cy="60" r="57" fill="#fff" stroke="var(--ring)" stroke-width="3"/><circle cx="60" cy="60" r="38" fill="var(--navy-tint)"/></svg></div>
    <p class="cell-text" style="top:36px;">Large scale events (cinema, theaters, sport, business con-ferences, etc.) should remain closed or operate virtually. Sport events can resume but without spectators. Athletes &amp; the staff surrounding them should be tested, disinfectants should be available &amp; masks used as much as reasonably possible.</p>
  </div>

</div>
</body>
</html>
```